Our company needs a Corporate Identity Package!!!

We would like to receive submissions for a corporate identity pachage including the following elements:

1. Presentation Folder
2. Product/Service Catalogue (16 A4 pages landscape but expandable)
3. Product Brochure (up to 8 A4 pages)
4. Product Flyer (2 A4 pages)
5. Business Card
6. Letterhead
7. Envelope
8. E-mail signature.

I attach a Presentation Folder that i like (geometric but also has circle). We would like to have some ideas regarding the above 7 elements including brindavex logo colors (brindavex.net).

Payment is indicative and we are planning to increase the payment now that we found out how to actually do this. You are also more than welcome to send us a message and suggest the amount of payment for your Corporate Identity elements and we will update this.

Target Market(s)

Home | Office | Life

Colors
f78f20
0555a3
9bcb3b

Requirements
Must have
• 1. Presentation Folder
• 2. Product/Service Catalogue (16 A4 pages landscape but to be easily expandable)
• 3. Product Brochure (up to 4 A4 pages but to be easily expandable )
• 4. Product Flyer (2 A4 pages)
• 5. Business Card
• 6. Letterhead
• 7. Envelope
• 8. E-mail signature.
Nice to have
• It would be nice to include design something around the cycle that communicates the best six doctors (i.e. sunshine, water, rest, air, exercise and diet) !!!

```html
<!DOCTYPE html>
<html lang="en">
<head>
<meta charset="utf-8">
<title>brindavex – Corporate Identity Set</title>
<link rel="stylesheet" href="https://fonts.googleapis.com/css2?family=Open+Sans:wght@400;600&display=swap">
<style>
  :root {
    --canvas: #ffffff;
    --navy: #1f2633;
    --navy-soft: #2c3546;
    --navy-line: #3a4457;
    --blue: #0a7fc4;
    --blue-light: #3aa6de;
    --green: #8cc63f;
    --orange: #f07f22;
    --paper: #ffffff;
    --paper-grey: #e6e9ec;
    --paper-grey-dark: #cfd4d9;
    --ink: #333a44;
    --ink-soft: #7a828c;
    --caption: #1a1a1a;
  }
  * { box-sizing: border-box; margin: 0; padding: 0; }
  html, body { width: 1200px; height: 540px; overflow: hidden; background: var(--canvas); }
  .sheet { position: relative; width: 1200px; height: 540px; font-family: "Open Sans", sans-serif; }
  .piece { position: absolute; }
  .piece svg { display: block; width: 100%; height: 100%; }
  .piece__art { position: absolute; left: 0; top: 0; box-shadow: 1px 2px 4px rgba(0,0,0,.25); background: var(--paper); }
  .piece__caption {
    position: absolute; text-align: center;
    font-size: 12.5px; color: var(--caption); white-space: nowrap;
  }
  .t { font-family: "Open Sans", sans-serif; }
  .brand-name { font-family: "Open Sans", sans-serif; font-weight: 600; }

  .card-back   { left: 23px;  top: 30px; }
  .card-front  { left: 321px; top: 30px; }
  .folder      { left: 621px; top: 5px; }
  .envelope    { left: 915px; top: 79px; }
  .lh-front    { left: 58px;  top: 222px; }
  .letterhead  { left: 361px; top: 226px; }
  .mark        { left: 664px; top: 244px; }
  .wordmark    { left: 915px; top: 360px; }
</style>
</head>
<body>
<main class="sheet">

  <!-- Business card, back -->
  <figure class="piece card-back">
    <div class="piece__art" style="width:258px;height:160px">
      <svg viewBox="0 0 258 160" aria-label="Business card back">
        <defs>
          <linearGradient id="cardGrey" x1="0" y1="0" x2="1" y2="1">
            <stop offset="0" stop-color="#f3f5f7"/><stop offset="1" stop-color="#cdd2d8"/>
          </linearGradient>
        </defs>
        <rect x="10" y="8" width="238" height="144" fill="url(#cardGrey)"/>
        <path d="M10 8 H92 C70 50 78 110 118 152 H10 Z" fill="var(--navy)"/>
        <path d="M92 8 C70 50 78 110 118 152" fill="none" stroke="var(--blue)" stroke-width="5"/>
        <path d="M10 118 C40 120 70 132 86 152 H10 Z" fill="var(--green)"/>
        <path d="M10 126 C40 128 64 138 78 152 H10 Z" fill="var(--navy)"/>
        <rect x="10" y="138" width="238" height="14" fill="var(--navy-soft)" opacity=".85"/>
        <circle cx="34" cy="58" r="10" fill="var(--blue)"/>
        <text x="22" y="84" class="brand-name" font-size="8.5" fill="#ffffff">brindavex</text>
        <text x="112" y="44" class="t" font-size="15" fill="var(--orange)">your name</text>
        <line x1="112" y1="51" x2="238" y2="51" stroke="var(--ink-soft)" stroke-width=".5"/>
        <g class="t" font-size="5.2">
          <text x="112" y="60" fill="var(--ink)" font-weight="600">PHONE</text>
          <text x="112" y="66" fill="var(--blue)">+123 456 78950</text>
          <text x="112" y="74" fill="var(--ink)" font-weight="600">SKYPE</text>
          <text x="112" y="80" fill="var(--blue)">myskypeidhere</text>
          <text x="112" y="88" fill="var(--ink)" font-weight="600">TWITTER</text>
          <text x="112" y="94" fill="var(--blue)">my_twitteridname</text>
          <text x="176" y="60" fill="var(--ink)" font-weight="600">FACEBOOK</text>
          <text x="176" y="66" fill="var(--blue)">myfacebookidname</text>
          <text x="176" y="74" fill="var(--ink)" font-weight="600">EMAIL</text>
          <text x="176" y="80" fill="var(--blue)">mymailid@domain.com</text>
          <text x="176" y="88" fill="var(--ink)" font-weight="600">WEBSITE</text>
          <text x="176" y="94" fill="var(--blue)">mywebsitedomain.com</text>
        </g>
        <line x1="112" y1="100" x2="238" y2="100" stroke="var(--ink-soft)" stroke-width=".5"/>
        <g class="t" font-size="6" fill="var(--ink)">
          <text x="112" y="110">There is your company's street address</text>
          <text x="112" y="118">with city, code &amp; country 58600</text>
        </g>
      </svg>
    </div>
    <figcaption class="piece__caption" style="top:168px;left:0;width:258px">03_Business Card_Back Side</figcaption>
  </figure>

  <!-- Business card, front -->
  <figure class="piece card-front">
    <div class="piece__art" style="width:258px;height:160px">
      <svg viewBox="0 0 258 160" aria-label="Business card front">
        <rect x="10" y="8" width="238" height="144" fill="var(--navy)"/>
        <path d="M10 8 H112 C72 22 44 60 28 108 C22 124 16 134 10 140 Z" fill="var(--paper-grey)"/>
        <path d="M112 8 C72 22 44 60 28 108 C22 124 16 134 10 140" fill="none" stroke="var(--blue)" stroke-width="6"/>
        <path d="M10 150 C20 140 28 126 34 112" fill="none" stroke="var(--green)" stroke-width="4"/>
        <rect x="10" y="140" width="238" height="12" fill="var(--navy-soft)"/>
        <circle cx="122" cy="74" r="8" fill="var(--blue)"/>
        <text x="135" y="79" class="brand-name" font-size="14" fill="#ffffff">brindavex</text>
        <g class="t" font-size="6.5" fill="#ffffff">
          <circle cx="94" cy="112" r="2.6" fill="var(--blue-light)"/><text x="100" y="114.5">facebookidname</text>
          <circle cx="94" cy="121" r="2.6" fill="var(--blue-light)"/><text x="100" y="123.5">twitteridname</text>
          <circle cx="94" cy="130" r="2.6" fill="var(--blue-light)"/><text x="100" y="132.5">www.mywebsite.com</text>
        </g>
      </svg>
    </div>
    <figcaption class="piece__caption" style="top:168px;left:0;width:258px">01_Business Card_Front Side_Deep</figcaption>
  </figure>

  <!-- Presentation folder -->
  <figure class="piece folder">
    <div class="piece__art" style="width:258px;height:186px">
      <svg viewBox="0 0 258 186" aria-label="Presentation folder">
        <rect width="258" height="186" fill="var(--paper-grey)"/>
        <path d="M0 0 H50 C34 8 16 22 0 34 Z" fill="var(--green)"/>
        <path d="M0 0 H42 C28 8 14 18 0 28 Z" fill="var(--navy)"/>
        <path d="M128 186 C160 150 200 110 258 92 V186 Z" fill="var(--navy)"/>
        <path d="M122 186 C156 148 198 106 258 88" fill="none" stroke="var(--blue)" stroke-width="6"/>
        <path d="M116 186 C148 152 188 114 258 98" fill="none" stroke="var(--green)" stroke-width="2"/>
        <line x1="129" y1="0" x2="129" y2="186" stroke="var(--paper-grey-dark)" stroke-width=".6"/>
        <circle cx="150" cy="28" r="7" fill="var(--blue)"/>
        <text x="161" y="32" class="brand-name" font-size="11" fill="var(--navy)">brindavex</text>
        <text x="44" y="76" class="t" font-size="4" fill="var(--ink)">Client name</text>
        <g stroke="var(--paper-grey-dark)" stroke-width=".6">
          <line x1="44" y1="82" x2="100" y2="82"/><line x1="44" y1="88" x2="100" y2="88"/>
          <line x1="44" y1="94" x2="100" y2="94"/><line x1="44" y1="100" x2="100" y2="100"/>
        </g>
        <circle cx="30" cy="124" r="11" fill="var(--blue)"/>
        <g class="t" font-size="3.6" fill="#ffffff">
          <circle cx="178" cy="130" r="1.6" fill="var(--blue-light)"/><text x="182" y="131.3">brindavex.net</text>
          <circle cx="178" cy="136" r="1.6" fill="var(--blue-light)"/><text x="182" y="137.3">hello@brindavex.net</text>
          <circle cx="178" cy="142" r="1.6" fill="var(--blue-light)"/><text x="182" y="143.3">+00 123 456</text>
        </g>
      </svg>
    </div>
    <figcaption class="piece__caption" style="top:194px;left:0;width:258px">01_Folder</figcaption>
  </figure>

  <!-- Envelope -->
  <figure class="piece envelope">
    <div class="piece__art" style="width:262px;height:110px">
      <svg viewBox="0 0 262 110" aria-label="Envelope">
        <rect width="262" height="110" fill="var(--paper-grey)"/>
        <path d="M6 14 H70 C58 40 52 70 56 96 H6 Z" fill="var(--navy)"/>
        <path d="M70 14 C58 40 52 70 56 96" fill="none" stroke="var(--blue)" stroke-width="3.5"/>
        <path d="M6 88 C20 88 34 92 40 96 H6 Z" fill="var(--green)"/>
        <circle cx="16" cy="24" r="4" fill="var(--blue)"/>
        <line x1="95" y1="8" x2="95" y2="102" stroke="var(--paper-grey-dark)" stroke-width=".6"/>
        <path d="M132 8 H256 V102 H220 C200 80 168 70 132 66 Z" fill="#f2f4f6"/>
        <path d="M222 102 C206 84 176 74 140 70" fill="none" stroke="var(--blue)" stroke-width="3"/>
        <rect x="138" y="30" width="48" height="18" rx="2" fill="var(--paper-grey-dark)"/>
        <circle cx="202" cy="28" r="3" fill="var(--blue)"/>
        <text x="208" y="30.5" class="brand-name" font-size="6.5" fill="var(--navy)">brindavex</text>
        <g class="t" font-size="3.4" fill="var(--ink)">
          <text x="104" y="26">Recipient name</text>
          <text x="104" y="32">Street and city</text>
        </g>
        <g class="t" font-size="3.2" fill="var(--ink-soft)">
          <text x="226" y="70">brindavex.net</text>
          <text x="226" y="75">hello@brindavex.net</text>
        </g>
      </svg>
    </div>
    <figcaption class="piece__caption" style="top:117px;left:0;width:262px">01_Envelop</figcaption>
  </figure>

  <!-- Letterhead, front cover -->
  <figure class="piece lh-front">
    <div class="piece__art" style="width:188px;height:262px">
      <svg viewBox="0 0 188 262" aria-label="Letterhead front">
        <rect width="188" height="262" fill="var(--paper)"/>
        <path d="M10 118 C40 80 110 56 178 54 V252 H10 Z" fill="var(--navy)"/>
        <path d="M10 118 C40 80 110 56 178 54" fill="none" stroke="var(--blue)" stroke-width="7"/>
        <path d="M80 70 C110 60 150 54 178 50" fill="none" stroke="var(--green)" stroke-width="4"/>
        <path d="M10 240 H178 V252 H10 Z" fill="var(--navy-soft)"/>
        <line x1="10" y1="240" x2="178" y2="240" stroke="var(--navy-line)" stroke-width=".6"/>
        <circle cx="40" cy="42" r="14" fill="var(--blue)"/>
        <g class="t" font-size="4.2" fill="#ffffff">
          <circle cx="64" cy="190" r="2" fill="var(--blue-light)"/><text x="69" y="191.5">facebookidname</text>
          <circle cx="64" cy="197" r="2" fill="var(--blue-light)"/><text x="69" y="198.5">twitteridname</text>
          <circle cx="64" cy="204" r="2" fill="var(--blue-light)"/><text x="69" y="205.5">www.mywebsite.com</text>
        </g>
      </svg>
    </div>
    <figcaption class="piece__caption" style="top:270px;left:0;width:188px">01_Letterhead_Front</figcaption>
  </figure>

  <!-- Letterhead -->
  <figure class="piece letterhead">
    <div class="piece__art" style="width:181px;height:258px">
      <svg viewBox="0 0 181 258" aria-label="Letterhead">
        <rect width="181" height="258" fill="var(--paper)"/>
        <path d="M6 14 C30 8 60 8 90 12" fill="none" stroke="var(--blue)" stroke-width="1.6"/>
        <circle cx="28" cy="28" r="5.5" fill="var(--blue)"/>
        <text x="37" y="31.5" class="brand-name" font-size="9" fill="var(--navy)">brindavex</text>
        <g class="t" font-size="3" fill="var(--ink-soft)">
          <text x="128" y="24">brindavex.net</text>
          <text x="128" y="29">hello@brindavex.net</text>
          <text x="128" y="34">+00 123 456 789</text>
        </g>
        <g class="t" font-size="3.6" fill="var(--ink)">
          <text x="22" y="58">Dear Client,</text>
          <text x="22" y="70">Thank you for choosing our home and office</text>
          <text x="22" y="76">services. We value your trust and support.</text>
          <text x="22" y="90">Our team is ready to help you plan</text>
          <text x="22" y="96">each step with care and clear advice.</text>
          <text x="22" y="110">We look forward to working with you.</text>
          <text x="22" y="126">Kind regards,</text>
          <path d="M24 146 C28 136 32 150 36 140 S44 146 48 142" fill="none" stroke="var(--ink)" stroke-width=".6"/>
          <text x="22" y="156">Alan Morris</text>
          <text x="22" y="161" fill="var(--ink-soft)">Office Manager</text>
        </g>
        <path d="M6 218 C60 206 120 206 175 220 V252 H6 Z" fill="var(--navy)"/>
        <path d="M6 218 C60 206 120 206 175 220" fill="none" stroke="var(--blue)" stroke-width="2.4"/>
        <g class="t" font-size="3" fill="#ffffff">
          <text x="40" y="236">12 Main Street, City</text>
          <text x="104" y="236">info@brindavex.net</text>
        </g>
      </svg>
    </div>
    <figcaption class="piece__caption" style="top:266px;left:0;width:181px">02_Letterhead</figcaption>
  </figure>

  <!-- Brand mark area -->
  <figure class="piece mark">
    <div class="piece__art" style="width:175px;height:238px">
      <svg viewBox="0 0 175 238" aria-label="Brand mark">
        <rect width="175" height="238" fill="var(--paper)"/>
        <circle cx="87" cy="104" r="48" fill="var(--blue)"/>
        <text x="87" y="180" text-anchor="middle" class="brand-name" font-size="20" fill="var(--navy)">brindavex</text>
      </svg>
    </div>
    <figcaption class="piece__caption" style="top:246px;left:0;width:175px">2</figcaption>
  </figure>

  <!-- Horizontal name lockup -->
  <figure class="piece wordmark">
    <div class="piece__art" style="width:262px;height:122px">
      <svg viewBox="0 0 262 122" aria-label="Horizontal name lockup">
        <rect width="262" height="122" fill="var(--paper)"/>
        <circle cx="54" cy="61" r="20" fill="var(--blue)"/>
        <text x="84" y="70" class="brand-name" font-size="26" fill="var(--navy)">brindavex</text>
      </svg>
    </div>
  </figure>

</main>
</body>
</html>
```